Refresh of far from plain IT company website

Our web site is starting to show it's age. You can see the existing site here: www.plumbwick.net. As a growing company we want to come across as a dynamic collection of IT experts.

We want to update the design so are open to any colour palette and look, but want to retain our current table logo. We use the logo on our business cards but with a white background - see the attached file, so you don't need to keep the brown or the green.

The design should consider the range of browsers that will be looking at the site - so please show how it will look on a wide screen laptop and a 768x1024 tablet.

We want to add some pages about our team and their skills, probably with photos of each person on the team.

This is an uncoded project - the PSD files of the design is required, not coding.
Updates

Thanks everyone for the submissions so far.  It's a holiday day in the UK today but we will get some feedback on the designs so far out to you.

Target Market(s)

Architects and other creative types looking for IT support

Industry/Entity Type

Business

Font styles to use
Serif
Sans Serif

Requirements
Must have
• Must look good on a laptop and an iPad.

```html
<!DOCTYPE html>
<html lang="en">
<head>
<meta charset="utf-8">
<title>plumbwick – IT Support</title>
<link rel="stylesheet" href="https://fonts.googleapis.com/css2?family=Ubuntu:wght@400;500;700&family=Oswald:wght@400;500&display=swap">
<style>
:root{
  --maroon:#8a0c52;
  --maroon-dark:#6a0b3f;
  --gold:#d4a800;
  --ink:#2b2b2b;
  --text:#3a3a3a;
  --grey-band:#ececec;
  --line:#cfcfcf;
  --white:#ffffff;
}
*{box-sizing:border-box;margin:0;padding:0}
html,body{width:974px;height:1200px;overflow:hidden;background:var(--white)}
body{position:relative;font-family:Arial,Helvetica,sans-serif;color:var(--text)}
.abs{position:absolute}

/* header */
.site-header{position:absolute;left:0;top:0;width:974px;height:101px;border-top:4px solid var(--gold);background:linear-gradient(#fff,#f1f1f1)}
.brand{position:absolute;left:108px;top:16px;display:flex;align-items:center;gap:14px}
.brand-mark{width:40px;height:40px;background:var(--gold)}
.brand-name{font-family:Ubuntu,sans-serif;font-weight:500;font-size:38px;color:var(--maroon);letter-spacing:-.5px}
.live-chat{position:absolute;left:729px;top:14px;width:131px;height:50px;border:1px solid #d8d8d8;border-radius:5px;background:linear-gradient(#fff,#ededed);display:flex;align-items:center}
.live-chat .agent{width:36px;height:46px;margin-left:6px;background:linear-gradient(#e9dccf,#bfa996);border-radius:3px}
.live-chat .label{font-family:Oswald,sans-serif;font-weight:500;font-size:16px;line-height:21px;margin-left:8px}
.live-chat .l1{color:var(--maroon)}
.live-chat .l2{color:#1f7a1f}
.main-nav{position:absolute;left:296px;top:74px;display:flex;font-family:Ubuntu,sans-serif;font-weight:500;font-size:12px;text-transform:uppercase}
.main-nav a{color:var(--maroon);text-decoration:none;padding:0 8.5px;height:23px;line-height:23px}
.main-nav a.current{background:#333;color:#fff;border-radius:3px 3px 0 0;padding:0 6px;margin-right:2px;font-size:13px}

/* hero */
.hero{position:absolute;left:0;top:101px;width:974px;height:360px;background:radial-gradient(ellipse at 72% 62%,#e69a4a 0%,#6b4b3a 18%,#243447 40%,#0b0f18 75%)}
.hero-caption{position:absolute;left:0;top:426px;width:974px;height:35px;background:rgba(0,0,0,.55)}
.hero-caption h2{font-family:Oswald,sans-serif;font-weight:400;font-size:22px;color:#fff;text-align:center;line-height:35px}
.dots{position:absolute;left:771px;top:436px;display:flex;gap:9px}
.dots span{width:14px;height:14px;border-radius:50%;background:var(--gold)}
.dots span:first-child{background:#fff}
.hero-rule{position:absolute;left:0;top:461px;width:974px;height:3px;background:#333}

/* section titles */
.section-title{position:absolute;left:0;width:974px;display:flex;justify-content:center;align-items:center;gap:10px;font-family:Ubuntu,sans-serif;font-weight:500;font-size:26px;color:var(--ink)}
.section-title em{font-style:normal;color:var(--maroon)}
.section-title .rule{width:210px;height:6px;border-top:1px solid #555;border-bottom:2px solid #333}

.about-text{position:absolute;left:120px;top:512px;width:734px;font-family:Ubuntu,sans-serif;font-size:11.2px;line-height:17px;text-align:center;color:var(--text)}
.more-link{position:absolute;left:0;top:587px;width:974px;text-align:center;font-family:Ubuntu,sans-serif;font-weight:500;font-size:12px;color:var(--maroon)}

/* services */
.services{position:absolute;left:0;top:606px;width:974px;height:218px;background:var(--grey-band);border-top:1px solid #ddd;border-bottom:1px solid #ddd}
.service{position:absolute;top:60px;width:140px;text-align:center}
.service .ring{width:90px;height:90px;margin:0 auto;border:4px solid var(--gold);border-radius:50%;background:#fff;display:flex;align-items:center;justify-content:center}
.service .glyph{width:46px;height:46px;border-radius:8px;background:var(--maroon)}
.service p{margin-top:18px;font-family:Ubuntu,sans-serif;font-weight:500;font-size:12px;color:var(--ink)}

/* columns */
.col{position:absolute;top:850px;width:230px}
.col h3{font-family:Ubuntu,sans-serif;font-weight:500;font-size:17.5px;color:var(--ink);display:flex;align-items:center;gap:7px;padding-bottom:6px;border-bottom:2px solid #ddd}
.col h3 em{font-style:normal;color:var(--maroon)}
.col h3 svg{width:18px;height:18px}
.news-item{margin-top:12px;font-size:10px;line-height:14px;color:#222}
.news-item b{display:block;font-size:10.5px;margin-bottom:5px}
.news-item + .news-item{border-top:1px dashed #ccc;padding-top:8px;margin-top:6px}
.read-more{display:block;text-align:right;font-weight:bold;font-size:10.5px;color:var(--maroon);margin-top:11px}
.quote{margin-top:15px;background:#ececec;border-radius:8px;padding:10px 14px 32px 16px;font-style:italic;font-size:10.5px;line-height:17px;color:#333;position:relative}
.quote .mark{font-size:30px;color:#c9c9c9;font-style:normal;line-height:0;position:relative;top:10px;margin-right:4px;font-family:Georgia,serif}
.client{display:flex;align-items:flex-end;gap:13px;margin-top:-26px;padding-left:16px;position:relative}
.client .photo{width:54px;height:54px;border:2px solid #fff;box-shadow:0 0 2px #999;background:linear-gradient(#6c7b8c,#2c3642)}
.client span{font-weight:bold;font-size:10px;color:#222;margin-bottom:12px}
.field{margin-top:13px;height:23px;border:1px solid #bbb;border-radius:3px;background:#fff;font-style:italic;font-size:10px;color:#666;padding:5px 8px}
.field + .field{margin-top:6px}
.field.msg{height:58px}
.submit{margin-top:13px;width:55px;height:20px;border-radius:2px;background:var(--maroon);color:#fff;font-weight:bold;font-size:12px;text-align:center;line-height:20px}

/* footer */
.site-footer{position:absolute;left:0;top:1075px;width:974px;height:125px;border-top:2px solid var(--gold);background:linear-gradient(#921655,#6b0d3e)}
.f-box{position:absolute;top:15px;height:63px;border:1px solid rgba(255,255,255,.18);background:rgba(255,255,255,.1);padding:6px 10px;color:#fff}
.f-box h4{font-size:12.5px;font-weight:bold;margin-bottom:6px}
.subscribe{display:flex;gap:6px}
.subscribe .input{width:146px;height:23px;border-radius:2px;background:rgba(255,255,255,.25);font-style:italic;font-size:10px;padding:5px 8px}
.subscribe .go{width:25px;height:23px;border-radius:2px;background:#3a0a24;display:flex;align-items:center;justify-content:center}
.contact-line{display:flex;align-items:center;gap:8px;font-size:10px;margin-bottom:4px}
.socials{display:flex;gap:12px;margin-top:2px}
.socials span{width:20px;height:20px;border-radius:3px;background:rgba(255,255,255,.55)}
.f-brand{position:absolute;left:648px;top:33px;display:flex;align-items:center;gap:14px}
.f-brand .sq{width:30px;height:30px;background:rgba(255,255,255,.55)}
.f-brand span{font-family:Ubuntu,sans-serif;font-weight:500;font-size:31px;color:rgba(255,255,255,.85)}
.f-links{position:absolute;left:115px;top:94px;font-size:10px;color:#fff}
.f-links i{font-style:normal;margin:0 7px}
.copyright{position:absolute;left:666px;top:94px;font-size:10px;color:#fff}
</style>
</head>
<body>

<header class="site-header">
  <div class="brand"><span class="brand-mark"></span><span class="brand-name">plumbwick</span></div>
  <div class="live-chat">
    <div class="agent" role="img" aria-label="Support agent photo"></div>
    <div class="label"><div class="l1">LIVE CHATT</div><div class="l2">AVAILABLE</div></div>
  </div>
  <nav class="main-nav">
    <a class="current">Home</a><a>About Us</a><a>What We Do</a><a>News Blog</a><a>Articles</a><a>Clients</a><a>Partners</a><a>Contact Us</a>
  </nav>
</header>

<section class="hero" role="img" aria-label="Hand holding a glowing table above a network of user icons"></section>
<div class="hero-caption"><h2>Serious IT Support For Business</h2></div>
<div class="dots"><span></span><span></span><span></span><span></span></div>
<div class="hero-rule"></div>

<h2 class="section-title" style="top:472px"><span class="rule"></span>About <em>plumbwick</em><span class="rule"></span></h2>
<p class="about-text">Plumbwick was established with a specific aim: to consistently deliver an advanced and comprehensive IT service for ambitious growing companies across many industry sectors. We aim to provide the very best in service and support, and to aid business growth through the effective and skilled use of modern IT solutions. Founded in 2003, we have grown rapidly and have delivered successful business solutions to small and medium sized businesses, working with customers across a wide IT spectrum. The knowledge...</p>
<div class="more-link">More +</div>

<section class="services">
  <h2 class="section-title" style="top:14px"><span class="rule"></span>Our <em>Services</em><span class="rule"></span></h2>
  <div class="service" style="left:120px"><div class="ring"><div class="glyph" role="img" aria-label="IT support icon"></div></div><p>It Support &amp; Management</p></div>
  <div class="service" style="left:273px"><div class="ring"><div class="glyph" role="img" aria-label="Cloud icon"></div></div><p>Cloud Computing</p></div>
  <div class="service" style="left:427px"><div class="ring"><div class="glyph" role="img" aria-label="Recovery icon"></div></div><p>Disaster Recovery</p></div>
  <div class="service" style="left:572px"><div class="ring"><div class="glyph" role="img" aria-label="Virtualisation icon"></div></div><p>Virtualisation</p></div>
  <div class="service" style="left:720px"><div class="ring"><div class="glyph" role="img" aria-label="CAD compass icon"></div></div><p>CAD Services</p></div>
</section>

<section class="col" style="left:115px">
  <h3><svg viewBox="0 0 18 18"><path d="M2 7h4l8-5v14l-8-5H2z" fill="#333"/></svg>Latest <em>News</em></h3>
  <div class="news-item"><b>04/17/2014</b>Lorem ipsum dolor sit amet, cctetuer adipiscingin elit, sed diam nummy nibh eui smod tinciduntiotvulputate velit esse olestie</div>
  <div class="news-item"><b>04/17/2014</b>Lorem ipsum dolor sit amet, cctetuer adipiscingin elit, sed diam nummy nibh eui smod tinciduntiotvulputate velit esse olestie</div>
  <span class="read-more">Read more »</span>
</section>

<section class="col" style="left:372px">
  <h3><svg viewBox="0 0 18 18"><path d="M1 2h11v8H5l-3 3v-3H1z M6 11h7l3 3v-3h1V5h-3v6" fill="#333"/></svg>Client <em>Testimonials</em></h3>
  <div class="quote"><span class="mark">“</span>Duis autem vel eum iriureol hder in vultat velit esse moles conqat vela ilu dolor feugiat.Duis autem vel eum ure hendrern vultat velit esse autm vel eum</div>
  <div class="client"><div class="photo" role="img" aria-label="Client portrait"></div><span>Mr. Dolore Eu Feugiat</span></div>
  <span class="read-more" style="margin-top:0">Read more »</span>
</section>

<section class="col" style="left:632px">
  <h3><svg viewBox="0 0 18 18"><path d="M2 2h9v3M2 2v14h11v-4" fill="none" stroke="#333" stroke-width="2"/><path d="M8 12l1-3 6-6 2 2-6 6z" fill="#333"/></svg>Quick <em>Contact</em></h3>
  <div class="field">Name</div>
  <div class="field">Email</div>
  <div class="field msg">Message</div>
  <div class="submit">Submit</div>
</section>

<footer class="site-footer">
  <div class="f-box" style="left:115px;width:199px">
    <h4>Subscribe to Newsletter</h4>
    <div class="subscribe"><div class="input">Email here</div><div class="go"><svg width="10" height="12" viewBox="0 0 10 12"><path d="M2 1l5 5-5 5" fill="none" stroke="#fff" stroke-width="2.5"/></svg></div></div>
  </div>
  <div class="f-box" style="left:337px;width:130px">
    <h4>Contact Us</h4>
    <div class="contact-line"><svg width="10" height="10" viewBox="0 0 10 10"><path d="M2 0l2 2-1 2 3 3 2-1 2 2-2 2C4 10 0 6 0 2z" fill="#e8a7c8"/></svg>012-555-0147</div>
    <div class="contact-line"><svg width="10" height="8" viewBox="0 0 10 8"><rect width="10" height="8" fill="#e8a7c8"/><path d="M0 0l5 4 5-4" fill="none" stroke="#7a1046"/></svg>info@plumbwick.com</div>
  </div>
  <div class="f-box" style="left:490px;width:96px">
    <h4>Follow Us</h4>
    <div class="socials"><span role="img" aria-label="Social profile"></span><span role="img" aria-label="Social profile"></span><span role="img" aria-label="News feed"></span></div>
  </div>
  <div class="f-brand"><span class="sq"></span><span>plumbwick</span></div>
  <div class="f-links">Home<i>|</i>About Us<i>|</i>What we do<i>|</i>News Blog<i>|</i>Articles<i>|</i>Clients<i>|</i>Partners<i>|</i>Terms<i>|</i>Support<i>|</i>Contact</div>
  <div class="copyright">© 2014 plumbwick. All Rights Reserved.</div>
</footer>

</body>
</html>
```